Business Card Design

Electronic Security Installation Specialists

Check out our website at www.tallbrookllc.com to see what we do.

Industry/Entity Type

Business

Contact Information for Business Card

Tall Brook
Marjorie Hadley
281 Orchard Rise
Mapleton, WV 25871

Colors
3176b5
0455a3
ffffff

```html
<!DOCTYPE html>
<html lang="en">
<head>
<meta charset="utf-8">
<title>Tall Brook — Business Card</title>
<link rel="stylesheet" href="https://fonts.googleapis.com/css2?family=Michroma&family=Exo+2:wght@400;600&display=swap">
<style>
  :root {
    --backdrop: #6e6e6e;
    --card: #ffffff;
    --card-shade: #ececec;
    --brand-blue: #0455a3;
    --brand-blue-light: #3176b5;
    --brand-blue-deep: #1b3f86;
    --steel: #8a8a8a;
    --steel-light: #d4d4d4;
    --ink: #3a3a3a;
    --ink-soft: #555555;
  }
  * { box-sizing: border-box; margin: 0; padding: 0; }
  html, body { width: 1200px; height: 750px; overflow: hidden; }
  body {
    background: var(--backdrop);
    font-family: "Exo 2", sans-serif;
    display: flex;
    align-items: center;
    justify-content: center;
    gap: 40px;
  }
  .card {
    position: relative;
    width: 540px;
    height: 309px;
    background: linear-gradient(135deg, var(--card) 40%, var(--card-shade));
    box-shadow: 0 10px 26px rgba(0,0,0,.35);
    overflow: hidden;
  }
  .brand {
    display: flex;
    align-items: center;
    gap: 10px;
    color: var(--brand-blue);
    font-family: "Exo 2", sans-serif;
    font-weight: 600;
  }
  .brand-dot {
    border-radius: 50%;
    background: var(--brand-blue);
  }
  /* Front */
  .card-front { display: flex; align-items: center; justify-content: center; }
  .card-front .brand { font-size: 34px; }
  .card-front .brand-dot { width: 34px; height: 34px; }

  /* Back */
  .card-back .accent-area {
    position: absolute;
    left: 0; right: 0; bottom: 0;
    height: 46px;
    background: linear-gradient(90deg, var(--brand-blue-deep), var(--brand-blue-light) 55%, var(--brand-blue) 78%, var(--steel) 100%);
  }
  .card-back .brand { position: absolute; left: 26px; top: 26px; font-size: 22px; }
  .card-back .brand-dot { width: 22px; height: 22px; }
  .identity {
    position: absolute; right: 30px; top: 30px; text-align: right;
    font-family: "Michroma", sans-serif; color: var(--ink);
  }
  .identity .person { font-size: 13px; letter-spacing: .5px; }
  .identity .role { font-size: 9px; color: var(--ink-soft); margin-top: 4px; letter-spacing: .5px; }
  .website {
    position: absolute; right: 30px; top: 104px;
    font-family: "Michroma", sans-serif; font-size: 9px; color: var(--ink);
  }
  .address {
    position: absolute; left: 26px; top: 72px; font-style: normal;
    font-family: "Michroma", sans-serif; font-size: 9.5px; line-height: 1.55; color: var(--ink);
  }
  .contact-list {
    position: absolute; left: 26px; top: 118px; list-style: none;
    font-family: "Michroma", sans-serif; font-size: 8.5px; color: var(--ink);
  }
  .contact-list li { display: flex; align-items: center; gap: 8px; height: 19px; }
  .contact-list svg { width: 11px; height: 11px; fill: var(--ink); }
</style>
</head>
<body>

  <section class="card card-front" aria-label="Card front">
    <div class="brand"><span class="brand-dot"></span><span>Tall Brook</span></div>
  </section>

  <section class="card card-back" aria-label="Card back">
    <div class="accent-area" role="img" aria-label="Decorative blue and grey curved band along the lower edge"></div>

    <div class="brand"><span class="brand-dot"></span><span>Tall Brook</span></div>

    <div class="identity">
      <p class="person">MARJORIE HADLEY</p>
      <p class="role">FINANCIAL ADVISOR</p>
    </div>
    <p class="website">www.tallbrookllc.com</p>

    <address class="address">
      281 Orchard Rise<br>Mapleton, WV 25871
    </address>

    <ul class="contact-list">
      <li><svg viewBox="0 0 12 12"><path d="M2.5 1h2l1 3-1.3 1a6 6 0 0 0 2.8 2.8l1-1.3 3 1v2c0 .6-.4 1-1 1A9.5 9.5 0 0 1 1.5 2c0-.6.4-1 1-1z"/></svg>304 555 0142</li>
      <li><svg viewBox="0 0 12 12"><path d="M3.5 0h5c.6 0 1 .4 1 1v10c0 .6-.4 1-1 1h-5c-.6 0-1-.4-1-1V1c0-.6.4-1 1-1zm.5 1.5v7.5h4V1.5z"/></svg>304 555 0187</li>
      <li><svg viewBox="0 0 12 12"><path d="M1 4h10v6H1zM3 1h6v3H3zM2.5 6h1.5v1.5H2.5zM5 6h1.5v1.5H5z"/></svg>304 555 0193</li>
      <li><svg viewBox="0 0 12 12"><path d="M1 2.5h10v7H1zM1.6 3 6 6.4 10.4 3" stroke="#fff" stroke-width=".8"/></svg>info@tallbrookllc.com</li>
    </ul>
  </section>

</body>
</html>
```